High-end law practice specializing in closely held business succession planning and complex estates

Solo practitioner whose practice specializes in high-net worth, complex estate planning needs muliple versions of letterhead black and white, please. Letterhead should incorporate slogan, "Protecting your family business is my business," for one and "Complex Estate Planning"; third with no slogan. All for The Law Office of Marcy Lynn Pettibone, PC, 418 Cedar Hollow Ln., Newport News, Virginia 23648, Tel. 757-555-0142 Fax tbd email: marcy@mlplawgroup.example; Marcy Lynn Pettibone, Esq., principal, licensed in VA, NY, DC
Updates

Project Deadline Extended
Reason: My internet service went down and I can only view designs on my smart phone -- it's just too hard to review. So sorry! Working with my ISP now. Please be patient!

Target Market(s)

High net worth clients with complex estate planning needs, family businesses, family farmers, family foresters -- people with unique estate/succession planning needs who need a specialist who understands them.

Industry/Entity Type

Business

Font styles to use
Script

Requirements
Must have
• A high-end look and feel, connoting trustworthiness, special knowledge, and expertise.

```html
<!DOCTYPE html>
<html lang="en">
<head>
<meta charset="utf-8">
<title>Letterhead – The Law Office of Marcy Lynn Pettibone, PC</title>
<link rel="stylesheet" href="https://fonts.googleapis.com/css2?family=Roboto+Slab:wght@300;400&family=Noto+Serif:wght@700&display=swap">
<style>
  :root {
    --ink: #333233;
    --paper: #ffffff;
    --placeholder: #e6e6e6;
    --frame: #3a3a3a;
  }
  html, body {
    margin: 0;
    padding: 0;
    width: 848px;
    height: 1200px;
    overflow: hidden;
    background: var(--paper);
  }
  .letterhead {
    position: relative;
    width: 848px;
    height: 1200px;
    box-sizing: border-box;
    border: 1px solid var(--frame);
    background: var(--paper);
    color: var(--ink);
    font-family: "Roboto Slab", Georgia, serif;
    overflow: hidden;
  }
  .monogram {
    position: absolute;
    left: 32px;
    top: 62px;
    width: 118px;
    height: 108px;
    display: flex;
    align-items: center;
    justify-content: center;
    font-family: "Noto Serif", Georgia, serif;
    font-weight: 700;
    font-size: 40px;
    color: var(--ink);
    letter-spacing: -1px;
  }
  .firm {
    position: absolute;
    left: 170px;
    top: 62px;
    line-height: 1;
  }
  .firm-intro {
    font-weight: 300;
    font-size: 24px;
    display: block;
  }
  .firm-name {
    font-family: "Noto Serif", Georgia, serif;
    font-weight: 700;
    font-size: 22px;
    display: block;
    margin-top: 4px;
  }
  .slogan {
    margin: 8px 0 0;
    font-weight: 300;
    font-size: 16.5px;
    line-height: 21px;
  }
  .practice-icons {
    position: absolute;
    left: 460px;
    top: 66px;
    width: 352px;
    height: 40px;
    background: var(--placeholder);
  }
  .credentials {
    position: absolute;
    left: 454px;
    top: 121px;
    width: 384px;
    height: 24px;
    background: var(--ink);
    color: var(--paper);
    font-size: 17.5px;
    font-weight: 300;
    line-height: 24px;
    padding-left: 12px;
    box-sizing: border-box;
  }
  .footer-band {
    position: absolute;
    left: 0;
    top: 1000px;
    width: 848px;
    height: 145px;
  }
  .contact {
    position: absolute;
    left: 0;
    top: 1078px;
    width: 846px;
    text-align: center;
    color: var(--paper);
    font-size: 14.5px;
    font-weight: 300;
    line-height: 28px;
  }
  .contact p { margin: 0; }
  .sep { margin: 0 6px; }
  .services {
    position: absolute;
    left: 0;
    top: 1151px;
    width: 846px;
    text-align: center;
    font-size: 14.5px;
    font-weight: 300;
    margin: 0;
  }
</style>
</head>
<body>
<div class="letterhead">
  <header>
    <div class="monogram">MLP</div>
    <div class="firm">
      <span class="firm-intro">The Law Office of</span>
      <span class="firm-name">Marcy Lynn Pettibone, PC</span>
      <p class="slogan">Protecting your family<br>business is my business.</p>
    </div>
    <div class="practice-icons" role="img" aria-label="Row of line icons for practice areas: oath, advocacy, gavel, scales of justice, financial documents, family, passport, handshake"></div>
    <div class="credentials">Esq., principal, licensed in VA, NY, DC</div>
  </header>

  <footer>
    <svg class="footer-band" viewBox="0 0 848 145" aria-hidden="true">
      <path d="M0 65 Q450 62 848 8 L848 145 L0 145 Z" fill="var(--ink)"/>
    </svg>
    <div class="contact">
      <p>Address: 418 Cedar Hollow Ln., Newport News, Virginia 23648,</p>
      <p>Telephone: 757-555-0142<span class="sep">|</span>Fax: 757-555-0199<span class="sep">|</span>E-mail: marcy@mlplawgroup.example<span class="sep">|</span>Website: www.mlplawgroup.example</p>
    </div>
    <p class="services">Estate Planning<span class="sep">|</span>Family Businesses<span class="sep">|</span>Family Farmers<span class="sep">|</span>Family Foresters<span class="sep">|</span>Unique Estate/Succession</p>
  </footer>
</div>
</body>
</html>
```